Home Remodeling company needs a business card design

we need a business card design for home remodeling company in hamilton county, indiana USA. we offers a wide range of construction services including whole house renovations, Design and Build Basements and Kitchen and Bathroom Remodeling . we would like to see designs for both site of business card that use the same color of the company logo and also including all information below :
1- Karim Feltous CEO / General Contractor
2- all company contacts Telephone numbers ( 1-888-DULOM-47 ) ( 317-555-0193) email address ( info@dulomhome.com) website ( www.dulomhome.com ) and social media logos (Facebook- twitter- google plus )
3- company logo
4- licensed . insured . bonded

```html
<!DOCTYPE html>
<html lang="en">
<head>
<meta charset="utf-8">
<title>Dulom Home Remodeling — Business Card</title>
<link rel="stylesheet" href="https://fonts.googleapis.com/css2?family=Cabin:wght@400;500;700&display=swap">
<style>
  :root {
    --page: #d9d9d9;
    --card: #f4f4f4;
    --ink: #2b2b2b;
    --ink-soft: #3c3c3c;
    --accent: #b3262e;
    --rule: #6a6a6a;
    --on-dark: #f4f4f4;
  }
  * { box-sizing: border-box; margin: 0; padding: 0; }
  html, body {
    width: 1105px; height: 1200px; overflow: hidden;
    background: var(--page);
    font-family: "Cabin", sans-serif;
    color: var(--ink);
  }
  .card {
    position: absolute; left: 182px; width: 746px; height: 425px;
    background: var(--card);
  }
  .card--front { top: 119px; }
  .card--back  { top: 637px; }

  /* front */
  .brand {
    position: absolute; left: 67px; top: 168px; width: 290px;
    color: var(--ink-soft); font-weight: 500;
  }
  .brand__name {
    display: block; font-size: 56px; line-height: 56px; letter-spacing: 3px;
  }
  .brand__tagline {
    display: block; font-size: 14px; line-height: 18px; letter-spacing: 5.2px;
    margin-top: 4px;
  }
  .divider {
    position: absolute; left: 394px; top: 122px; width: 1.5px; height: 183px;
    background: var(--rule);
  }
  .person { position: absolute; left: 435px; top: 118px; }
  .person__name { font-weight: 700; font-size: 27px; color: var(--ink); }
  .person__role { font-size: 21px; color: var(--accent); margin-top: 2px; }
  .contacts { list-style: none; margin-top: 22px; }
  .contacts li {
    display: flex; align-items: center; gap: 10px;
    font-size: 19px; color: var(--ink-soft); height: 29px;
  }
  .contacts svg { width: 17px; height: 17px; fill: var(--ink); flex: none; }

  /* back */
  .emblem {
    position: absolute; left: 307px; top: 91px; width: 131px; height: 133px;
    background: var(--accent);
  }
  .credentials {
    position: absolute; left: 0; right: 0; top: 262px;
    text-align: center; font-size: 21px; color: var(--accent); letter-spacing: .3px;
  }
  .services {
    position: absolute; left: 0; right: 0; top: 298px;
    text-align: center; font-size: 17.5px; line-height: 23px; color: var(--ink-soft);
  }
  .social {
    position: absolute; left: 0; right: 0; top: 355px;
    display: flex; justify-content: center; align-items: center; gap: 4px;
  }
  .social__line { width: 62px; height: 1px; background: var(--rule); margin: 0 6px; }
  .social__icon {
    width: 27px; height: 27px; border-radius: 50%; background: var(--ink);
    display: flex; align-items: center; justify-content: center;
  }
  .social__icon svg { width: 15px; height: 15px; fill: var(--on-dark); }
</style>
</head>
<body>
  <section class="card card--front">
    <div class="brand">
      <span class="brand__name">DULOM</span>
      <span class="brand__tagline">HOME REMODELING</span>
    </div>
    <div class="divider"></div>
    <div class="person">
      <h1 class="person__name">Karim Feltous</h1>
      <p class="person__role">CEO / General Contractor</p>
      <ul class="contacts">
        <li><svg viewBox="0 0 24 24"><path d="M6.6 10.8a15 15 0 0 0 6.6 6.6l2.2-2.2c.3-.3.7-.4 1-.2 1.1.4 2.3.6 3.6.6.6 0 1 .4 1 1V20c0 .6-.4 1-1 1A17 17 0 0 1 3 4c0-.6.4-1 1-1h3.5c.6 0 1 .4 1 1 0 1.3.2 2.5.6 3.6.1.3 0 .7-.2 1z"/></svg>1-888-DULOM-47</li>
        <li><svg viewBox="0 0 24 24"><path d="M7 1h10a2 2 0 0 1 2 2v18a2 2 0 0 1-2 2H7a2 2 0 0 1-2-2V3a2 2 0 0 1 2-2zm0 3v15h10V4z"/></svg>317-555-0193</li>
        <li><svg viewBox="0 0 24 24"><path d="M2 5h20v14H2zm2 2v.4l8 5.2 8-5.2V7z"/></svg>info@dulomhome.com</li>
        <li><svg viewBox="0 0 24 24"><path d="M12 2a10 10 0 1 0 0 20 10 10 0 0 0 0-20zm-1 17.9A8 8 0 0 1 4.1 10L9 15v1a2 2 0 0 0 2 2zm6.9-2.5A2 2 0 0 0 16 16h-1v-3a1 1 0 0 0-1-1H8v-2h2a1 1 0 0 0 1-1V7h2a2 2 0 0 0 2-2v-.4a8 8 0 0 1 2.9 12.8z"/></svg>www.dulomhome.com</li>
      </ul>
    </div>
  </section>

  <section class="card card--back">
    <div class="emblem"></div>
    <p class="credentials">LICENSED | INSURED | BONDED</p>
    <p class="services">Construction services | Whole house renovations<br>Design &amp; Build Basements | Kitchen &amp; Bathroom Remodeling</p>
    <div class="social">
      <span class="social__line"></span>
      <span class="social__icon" aria-label="Chat"><svg viewBox="0 0 24 24"><path d="M4 3h16a2 2 0 0 1 2 2v10a2 2 0 0 1-2 2H9l-5 4v-4a2 2 0 0 1-2-2V5a2 2 0 0 1 2-2z"/></svg></span>
      <span class="social__icon" aria-label="Share"><svg viewBox="0 0 24 24"><circle cx="18" cy="5" r="3"/><circle cx="6" cy="12" r="3"/><circle cx="18" cy="19" r="3"/><path d="M7.5 11l9-5 1 1.7-9 5zM8.5 11.3l9 5-1 1.7-9-5z"/></svg></span>
      <span class="social__icon" aria-label="Link"><svg viewBox="0 0 24 24"><path d="M10.6 13.4a1 1 0 0 1 0-1.4l3.5-3.5a1 1 0 1 1 1.4 1.4L12 13.4a1 1 0 0 1-1.4 0zM6.3 20.5a4.2 4.2 0 0 1-3-7.2l3-3 1.4 1.4-3 3a2.2 2.2 0 1 0 3.1 3.1l3-3 1.4 1.4-3 3a4.2 4.2 0 0 1-2.9 1.3zm11.4-6.9-1.4-1.4 3-3a2.2 2.2 0 1 0-3.1-3.1l-3 3-1.4-1.4 3-3a4.2 4.2 0 0 1 5.9 5.9z"/></svg></span>
      <span class="social__line"></span>
    </div>
  </section>
</body>
</html>
```